Etiketten-Design für Kaffeetüten
Zielgruppe
Wir stellen eine nachhaltige alternative zu herkömmlichem Bohnenkaffee her.
Regional, nachhaltig und koffeinfrei.
Hierzu verwenden wir Süßlupinen die wir von einem Partnerbauern aus Niedersachsen beziehen. Diese Lupinen werden wie herkömmlicher Kaffee in einem Trommelröster geröstet und anschließend gemahlen.
Unser Lupinenkaffee kann wie herkömmlicher Kaffee im Filter in der Frenchpress oder in einem Espressokocher zubereitet werden.
Wir bieten unseren Kunden zwei verschiedene Sorten an, eine 'Mild' und eine 'Klassisch'.
Die Zielgruppe sind ernährungsbewusste Menschen die gezielt eine alternative zu herkömmlichen Bohnenkaffee suchen. (Koffeinfreier Kaffee, Getreidekaffee)
Aufgabenstellung
Wir möchten ein modernes Design des Etiketts, das den Stil des Logos widerspiegelt. Die beiden Sorten 'Mild' und 'Klassisch' sollten gut von einander zu unterscheiden sein.
Es gibt ein Etikett für die Vorderseite, hier soll die Produktbezeichnung 'Lupinenkaffee' sowie die Mengenangabe '500g' stehen.
Ggf. 3 Icons für mögliche Brühmethoden (Filter, Frenchpress, Espressokocher)
Auf dem Etikett der Rückseite müssen zum einen die Zutaten, die Zubereitung sowie die Nährwertangaben (in TabellenForm) angegeben werden. Sowie ein EAN Code die Herstellerangaben und die Adresse der Homepage.
TREVO KAFFEE – Deine nachhaltige Kaffeealternative
Zutaten: weiße Süßlupinen, geröstet
Zubereitung: Du kannst Deinen Lupinenkaffee mit der French Press, dem klassischen Filter oder dem Espressokocher zubereiten. Für den optimalen Geschmack empfehlen wir 8g Kaffeepulver für 100ml.
Hersteller:
TREVO GmbH
Henrietta-Lenz-Weg 47
40477 Düsseldorf
www.TREVOKAFFEE.de
 Nährwertangaben für 100 ml Kaffee
Energie 12kj - 5 kcal
Fett <0,1g
Davon gesättigt <0,1g
Kohlenhydrate <1,0g
Davon Zucker <0,05g
Eiweiß <1,0g
Salz <0,05g
Die Kaffeetüte, auf die das Etikett geklebt wird, ist in einer braunen Kartonfarbe.
Das Etikett für die Kaffeetüten hat die Maße 7x11.
Das Logo hat die Schriftart 'Cera'. Die verwendete Schriftart sollte möglichst gleich sein, oder gut damit harmonieren.

```html
<!DOCTYPE html>
<html lang="de">
<head>
<meta charset="utf-8">
<title>Lupinenkaffee Etiketten – Classic &amp; Mild</title>
<link rel="stylesheet" href="https://fonts.googleapis.com/css2?family=Ubuntu:wght@400;500;700&family=Ubuntu+Condensed&display=swap">
<style>
  :root{
    --stage:#e4e5e3;
    --kraft:#c8a378;
    --kraft-dark:#b8936a;
    --ink-light:#ffffff;
    --ink-dark:#454545;
    --classic:#cc0080;
    --mild:#779a6b;
  }
  *{margin:0;padding:0;box-sizing:border-box}
  html,body{width:1200px;height:903px;overflow:hidden;background:var(--stage)}
  body{position:relative;font-family:"Ubuntu",sans-serif;color:var(--ink-light)}

  .pouch{
    position:absolute;top:54px;width:484px;height:809px;
    background:linear-gradient(180deg,var(--kraft) 0%,var(--kraft-dark) 100%);
    overflow:hidden;
  }
  .pouch--classic{left:43px;--accent:var(--classic)}
  .pouch--mild{left:655px;--accent:var(--mild)}

  .zip-line{position:absolute;left:0;right:0;top:124px;height:4px;background:rgba(255,255,255,.18)}

  .band{position:absolute;top:0;left:303px;width:62px;height:809px;background:var(--accent)}
  .pouch--mild .band{left:305px}
  .band svg{display:block;width:62px;height:809px;overflow:hidden}
  .band .product-name{font-family:"Ubuntu Condensed",sans-serif;font-size:88px;fill:var(--ink-dark)}

  .brand{position:absolute;top:24px;left:0;width:62px;text-align:center;
    font-family:"Ubuntu",sans-serif;font-weight:400;color:var(--ink-light)}
  .brand-dot{width:40px;height:40px;border:1.5px solid var(--ink-light);border-radius:50%;margin:0 auto 10px}
  .brand-name{font-size:10px;letter-spacing:2px;line-height:13px}

  .copy{position:absolute;right:192px;top:318px;text-align:right;white-space:nowrap}
  .pouch--mild .copy{right:189px}
  .variety{font-weight:700;font-size:38px;line-height:44px;letter-spacing:.5px}
  .tagline{font-family:"Ubuntu Condensed",sans-serif;font-size:21px;line-height:27px;margin-top:1px}
  .claims{list-style:none;font-family:"Ubuntu Condensed",sans-serif;font-size:21px;line-height:28px;margin-top:28px}

  .brew-icons{display:flex;justify-content:flex-end;align-items:flex-end;gap:10px;margin-top:20px}
  .brew-icons svg{stroke:var(--ink-light);fill:none;stroke-width:1.6;stroke-linejoin:round;stroke-linecap:round}
</style>
</head>
<body>

<section class="pouch pouch--classic" aria-label="Etikett Classic">
  <div class="zip-line"></div>
  <div class="copy">
    <h2 class="variety">CLASSIC</h2>
    <p class="tagline">Deine nachhaltige<br>Kaffeealternative</p>
    <ul class="claims"><li>Koffeinfrei</li><li>Vegan</li><li>Glutenfrei</li></ul>
    <div class="brew-icons">
      <svg width="36" height="42" viewBox="0 0 36 42" aria-label="Espressokocher"><path d="M9 4h14l2 4H7z M7 8h18l-3 12H10z M10 20h12l4 20H6z M25 10h6v10h-5 M14 27h8 M13 27l-2 11 M23 27l2 11"/></svg>
      <svg width="58" height="42" viewBox="0 0 58 42" aria-label="Filter"><path d="M3 12Q29-4 55 12L33 40H25Z M8 15Q29 4 50 15"/></svg>
      <svg width="36" height="42" viewBox="0 0 36 42" aria-label="French Press"><path d="M16 1v6 M12 2h8 M6 7h20v32H6z M4 39h24 M26 12h6v20h-6 M16 10v18 M10 28h12"/></svg>
    </div>
  </div>
  <div class="band">
    <div class="brand"><div class="brand-dot"></div><p class="brand-name">TREVO<br>KAFFEE</p></div>
    <svg viewBox="0 0 62 809" aria-hidden="false">
      <text class="product-name" transform="translate(62,583) rotate(-90)" x="0" y="0" textLength="455" lengthAdjust="spacingAndGlyphs">LUPPINENKAFFEE</text>
    </svg>
  </div>
</section>

<section class="pouch pouch--mild" aria-label="Etikett Mild">
  <div class="zip-line"></div>
  <div class="copy">
    <h2 class="variety">MILD</h2>
    <p class="tagline">Deine nachhaltige<br>Kaffeealternative</p>
    <ul class="claims"><li>Koffeinfrei</li><li>Vegan</li><li>Glutenfrei</li></ul>
    <div class="brew-icons">
      <svg width="36" height="42" viewBox="0 0 36 42" aria-label="Espressokocher"><path d="M9 4h14l2 4H7z M7 8h18l-3 12H10z M10 20h12l4 20H6z M25 10h6v10h-5 M14 27h8 M13 27l-2 11 M23 27l2 11"/></svg>
      <svg width="58" height="42" viewBox="0 0 58 42" aria-label="Filter"><path d="M3 12Q29-4 55 12L33 40H25Z M8 15Q29 4 50 15"/></svg>
      <svg width="36" height="42" viewBox="0 0 36 42" aria-label="French Press"><path d="M16 1v6 M12 2h8 M6 7h20v32H6z M4 39h24 M26 12h6v20h-6 M16 10v18 M10 28h12"/></svg>
    </div>
  </div>
  <div class="band">
    <div class="brand"><div class="brand-dot"></div><p class="brand-name">TREVO<br>KAFFEE</p></div>
    <svg viewBox="0 0 62 809">
      <text class="product-name" transform="translate(62,585) rotate(-90)" x="0" y="0" textLength="455" lengthAdjust="spacingAndGlyphs">LUPPINENKAFFEE</text>
    </svg>
  </div>
</section>

</body>
</html>
```